World Wide News and Current Affairs website

We intends to start up a new website which deals on New and Current Affairs.
Attention Designers,
We want a home page design for this project. Our business is based in the United States. Our goal is to become a well known brand.
The website would consist of a category for News, Business and Tech.
The theme should be beautiful and attention seeking. The website would take bulk of it's news from the US, and Europe.
Designers can get inspiration from already existing new websites such as PWJ, KLV, DASKOLM.
All designs should be clean and easy to navigate.

```html
<!DOCTYPE html>
<html lang="en">
<head>
<meta charset="utf-8">
<title>Meridian — News and Current Affairs</title>
<link href="https://fonts.googleapis.com/css2?family=Roboto:wght@400;500;700&family=Open+Sans:wght@400;600;700&display=swap" rel="stylesheet">
<style>
:root{
  --red:#d9100f;
  --red-dark:#b70c0b;
  --ink:#222;
  --muted:#666;
  --black:#111;
  --panel:#1c1c1c;
  --grey-bg:#e9e9e4;
  --white:#fff;
  --line:#ddd;
}
*{box-sizing:border-box;margin:0;padding:0}
html,body{width:1200px;height:3830px;overflow:hidden}
body{font-family:"Open Sans",Arial,sans-serif;color:var(--ink);background:var(--white);position:relative}
.sec{position:absolute;left:0;width:1200px}
.abs{position:absolute}
.h-sec{font-family:"Roboto",Arial,sans-serif;font-size:34px;font-weight:400;color:var(--ink);padding-left:14px;border-left:5px solid var(--red);line-height:32px}
.ph{display:block}
.meta{display:flex;gap:22px;font-size:12px;color:#777;align-items:center}
.meta span{display:flex;align-items:center;gap:6px}
.ic{width:13px;height:13px}

.trend{top:0;height:46px;background:var(--black);color:#fff;display:flex;align-items:center}
.trend .tag{margin-left:77px;background:var(--red);font:700 13px "Roboto",sans-serif;padding:6px 14px;display:flex;gap:6px;align-items:center}
.trend .txt{margin-left:18px;font:700 15px "Roboto",sans-serif}
.trend .arrows{margin-left:auto;margin-right:77px;display:flex;gap:10px}
.circ{width:28px;height:28px;border:2px solid #fff;border-radius:50%;display:flex;align-items:center;justify-content:center}

.nav{top:46px;height:77px;background:#fff;display:flex;align-items:center}
.brand{margin-left:77px;font:700 34px "Roboto",sans-serif;color:var(--red)}
.menu{margin-left:auto;display:flex;margin-right:77px;align-items:center;height:100%}
.menu a{font:400 17px "Roboto",sans-serif;color:#333;text-decoration:none;padding:0 21px;height:100%;display:flex;align-items:center}
.menu a.on{color:var(--red);box-shadow:inset 0 -3px 0 var(--red)}

.hero{top:123px;height:472px;background:var(--panel)}
.hero .photo{left:0;top:0;width:600px;height:472px;background:linear-gradient(135deg,#9c9c9c,#5a5a5a 55%,#c8c8c8)}
.hero .body{left:638px;top:35px;width:484px;color:#fff}
.badge{display:inline-block;background:var(--red);color:#fff;font:500 12px "Roboto",sans-serif;padding:5px 11px;text-transform:uppercase}
.hero h1{font:700 32px/38px "Roboto",sans-serif;margin-top:22px}
.hero p{font-size:15px;line-height:26px;color:#ddd;margin-top:24px}
.hero .rule{height:2px;background:#ccc;margin-top:28px}
.hero .foot{display:flex;align-items:center;margin-top:24px;font-size:12px}
.hero .foot b{font-weight:700;letter-spacing:.3px}
.hero .foot .meta{margin-left:auto;color:#ddd}
.hero .dots{left:562px;top:417px;display:flex;gap:8px}
.hero .dots .circ{width:30px;height:30px;border-color:#bbb;background:rgba(0,0,0,.3)}

.latest{top:595px;height:929px;background:var(--grey-bg)}
.tabs{right:79px;top:55px;display:flex;gap:30px;font-size:15px;color:#777}
.tabs .on{color:#333;border-bottom:2px solid var(--red);padding-bottom:6px}
.card{position:absolute;top:138px;width:332px;height:334px;background:#fff}
.card .ph{height:186px}
.card .in{padding:16px 30px}
.card h3{font:400 16px "Roboto",sans-serif;color:var(--red)}
.card p{font-size:14px;line-height:22px;color:#555;margin-top:4px}
.card .meta{margin-top:20px}
.mini{position:absolute;width:332px;height:107px;display:flex;gap:14px}
.mini .ph{width:153px;height:107px;flex:none}
.mini h4{font:400 15px "Roboto",sans-serif;color:var(--red)}
.mini .d{font-size:12px;color:#777;margin-top:4px;display:flex;gap:6px;align-items:center}
.mini p{font-size:14px;line-height:22px;color:#555;margin-top:8px}
.subscribe{left:789px;top:510px;width:332px;height:368px;background:var(--panel);color:#fff;text-align:center;padding:30px 22px}
.subscribe h3{font:400 36px "Roboto",sans-serif;color:var(--red)}
.subscribe p{font-size:14px;line-height:22px;color:#ccc;margin-top:18px}
.field{height:42px;background:#fff;color:#999;font-size:13px;text-align:left;padding:0 18px;display:flex;align-items:center;margin-top:18px}
.btn{background:var(--red);color:#fff;font:700 17px "Roboto",sans-serif;height:42px;display:flex;align-items:center;justify-content:center;margin-top:18px;text-transform:uppercase}

.stories{top:1524px;height:462px;background:#fff}
.story{position:absolute;top:125px;width:511px;height:286px}
.story .cap{position:absolute;left:24px;bottom:18px;right:24px;color:#fff}
.story h3{font:700 22px "Roboto",sans-serif}
.story p{font-size:14px;line-height:22px;margin-top:6px}
.story .cat{font-size:14px;margin-top:10px;border-left:3px solid var(--red);padding-left:8px}

.video{top:1986px;height:832px;background:var(--grey-bg)}
.player{left:77px;top:133px;width:1044px;height:421px;background:linear-gradient(180deg,#3a3e58 0%,#6e5a5c 45%,#2a2020 100%)}
.play{left:492px;top:176px}
.player .cap{left:30px;top:272px;color:#fff}
.player .cap .d{font-size:13px;margin-top:14px;display:flex;gap:6px;align-items:center}
.player .cap h3{font:500 32px "Roboto",sans-serif;margin-top:8px}
.vbar{left:77px;top:554px;width:1044px;height:225px;background:var(--red-dark)}
.vtabs{display:flex;gap:40px;padding:13px 30px 0;font:700 20px "Roboto",sans-serif;color:#fff;border-bottom:1px solid rgba(255,255,255,.35);height:54px}
.vtabs .on{border-bottom:4px solid #fff;padding:0 0 10px}
.vitems{display:flex;gap:28px;padding:24px 0 0 30px}
.vitem{display:flex;gap:14px;width:330px}
.vitem .ph{width:155px;height:102px}
.vitem h4{font:500 24px "Roboto",sans-serif;color:#fff}
.vitem .d{font-size:12px;color:#fff;display:flex;gap:6px;align-items:center;margin-top:4px}
.vitem .lbl{display:inline-block;background:#111;color:#fff;font:700 13px "Roboto",sans-serif;padding:4px 20px;margin-top:10px}
.vnext{right:0;top:100px;width:22px;height:80px;background:#222;display:flex;align-items:center;justify-content:center}

.editor{top:2818px;height:348px;background:#fff}
.redcirc{width:30px;height:30px;border:2px solid var(--red);border-radius:50%;display:flex;align-items:center;justify-content:center}
.strip{left:0;top:138px;width:1200px;height:206px;display:flex}
.strip .ph{width:240px;height:206px;position:relative}
.strip .ov{position:absolute;inset:0;background:rgba(200,15,15,.82);color:#fff;padding:24px 30px}
.strip .ov h4{font:700 20px "Roboto",sans-serif}
.strip .ov .d{font-size:13px;margin-top:6px}
.strip .ov p{font-size:14px;line-height:22px;margin-top:8px}

.stay{top:3166px;height:240px;background:var(--grey-bg);text-align:center}
.stay h2{display:inline-block;margin-top:46px}
.stay p{font-size:14px;color:#666;margin-top:16px}
.stay .row{display:flex;justify-content:center;gap:16px;margin-top:22px}
.stay .f{width:288px;height:41px;background:#fff;color:#999;font-size:13px;display:flex;align-items:center;padding:0 18px;text-align:left}
.stay .b{width:136px;height:41px;background:var(--red);color:#fff;font:700 20px "Roboto",sans-serif;display:flex;align-items:center;justify-content:center}

.weather{top:3406px;height:82px;background:var(--red);color:#fff;display:flex;align-items:center;font-size:15px}
.weather .loc{margin-left:77px}
.weather .tmp{margin-left:28px;display:flex;gap:16px;align-items:center}
.search{margin-left:auto;margin-right:79px;display:flex}
.search .f{width:215px;height:34px;border:1px solid #fff;font-size:13px;display:flex;align-items:center;padding:0 10px}
.search .g{width:34px;height:34px;background:#111;display:flex;align-items:center;justify-content:center}

.footer{top:3488px;height:296px;background:var(--black);color:#fff}
.col{position:absolute;top:36px;width:240px}
.col h5{font:400 18px "Roboto",sans-serif;border-left:4px solid var(--red);padding-left:12px;line-height:18px}
.col ul{list-style:none;margin-top:28px}
.col li{font-size:14px;line-height:33px;color:#ddd}
.bottom{top:3784px;height:46px;background:var(--red);color:#fff;display:flex;align-items:center;font-size:14px}
.bottom .copy{margin-left:77px}
.bottom .links{margin-left:auto;margin-right:77px;display:flex}
.bottom .links span{padding:0 12px;border-left:1px solid rgba(255,255,255,.6)}
.bottom .links span:first-child{border-left:none}
</style>
</head>
<body>

<svg width="0" height="0" style="position:absolute">
  <defs>
    <symbol id="i-cal" viewBox="0 0 14 14"><rect x="1" y="2" width="12" height="11" fill="none" stroke="#d9100f" stroke-width="1.5"/><rect x="1" y="2" width="12" height="3" fill="#d9100f"/></symbol>
    <symbol id="i-com" viewBox="0 0 14 14"><path d="M2 2h10v7H6l-3 3V9H2z" fill="none" stroke="#d9100f" stroke-width="1.5"/></symbol>
    <symbol id="i-heart" viewBox="0 0 14 14"><path d="M7 12S1.5 8.5 1.5 5A2.8 2.8 0 0 1 7 3.6 2.8 2.8 0 0 1 12.5 5C12.5 8.5 7 12 7 12z" fill="none" stroke="#d9100f" stroke-width="1.5"/></symbol>
    <symbol id="i-l" viewBox="0 0 10 10"><path d="M6.5 1.5 3 5l3.5 3.5" fill="none" stroke="currentColor" stroke-width="1.8"/></symbol>
    <symbol id="i-r" viewBox="0 0 10 10"><path d="M3.5 1.5 7 5 3.5 8.5" fill="none" stroke="currentColor" stroke-width="1.8"/></symbol>
  </defs>
</svg>

<header class="sec trend">
  <div class="tag"><svg width="10" height="13" viewBox="0 0 10 13"><path d="M6 0 0 7h4l-1 6 7-8H6z" fill="#fff"/></svg>TRENDING</div>
  <div class="txt">News Title : Lorem Ipsum is simply dummy text of the printing and typesetting industry.</div>
  <div class="arrows">
    <div class="circ" style="color:#fff"><svg width="12" height="12"><use href="#i-l"/></svg></div>
    <div class="circ" style="color:#fff"><svg width="12" height="12"><use href="#i-r"/></svg></div>
  </div>
</header>

<nav class="sec nav">
  <div class="brand">Meridian</div>
  <div class="menu">
    <a class="on">HOME</a><a>ABOUT US</a><a>NEWS</a><a>BUSINESS</a><a>TECHNOLOGY</a><a>VIDEO</a>
    <a style="padding-right:0"><svg width="18" height="18" viewBox="0 0 18 18"><circle cx="7.5" cy="7.5" r="5.5" fill="none" stroke="#333" stroke-width="2"/><path d="M12 12l5 5" stroke="#333" stroke-width="2"/></svg></a>
  </div>
</nav>

<section class="sec hero">
  <div class="abs photo" role="img" aria-label="Businessman in a suit standing before a city skyline with data graphics"></div>
  <div class="abs body">
    <span class="badge">Top News</span>
    <h1>In Our Ever-Increasing Digital Society, The technology...</h1>
    <p>Lorem Ipsum is simply dummy text of the printing and typesetting industry. Lorem Ipsum has been the industry's standard dummy text ever since the 1500s, when an unknown printer took a galley of type and scrambled it to make a type specimen book. It has survived not only five centuries, but [...]</p>
    <div class="rule"></div>
    <div class="foot"><b>CONTINUE READING</b>
      <div class="meta"><span><svg class="ic"><use href="#i-cal"/></svg>April 22nd, 2017</span><span><svg class="ic"><use href="#i-com"/></svg>4</span><span><svg class="ic"><use href="#i-heart"/></svg>134</span></div>
    </div>
  </div>
  <div class="abs dots">
    <div class="circ" style="color:#ddd"><svg width="12" height="12"><use href="#i-l"/></svg></div>
    <div class="circ" style="color:#ddd"><svg width="12" height="12"><use href="#i-r"/></svg></div>
  </div>
</section>

<section class="sec latest">
  <h2 class="abs h-sec" style="left:77px;top:52px">All The Latest News</h2>
  <div class="abs tabs"><span class="on">News</span><span>Business</span><span>Technology</span></div>

  <article class="card" style="left:77px">
    <div class="ph" role="img" aria-label="City skyline at night with a person using a tablet" style="background:linear-gradient(180deg,#1b2240,#4a4f7a 60%,#c07a4a)"></div>
    <div class="in"><h3>News Title</h3><p>Lorem Ipsum is simply dummy text of the printing and typesetting industry.</p>
      <div class="meta"><span><svg class="ic"><use href="#i-cal"/></svg>April 21st, 2017</span><span><svg class="ic"><use href="#i-com"/></svg>4</span><span><svg class="ic"><use href="#i-heart"/></svg>134</span></div></div>
  </article>
  <article class="card" style="left:434px">
    <div class="ph" role="img" aria-label="Two leaders seated in conversation in an office" style="background:linear-gradient(180deg,#c9b48a,#7a6a55 60%,#3a3530)"></div>
    <div class="in"><h3>News Title</h3><p>Lorem Ipsum is simply dummy text of the printing and typesetting industry.</p>
      <div class="meta"><span><svg class="ic"><use href="#i-cal"/></svg>April 21st, 2017</span><span><svg class="ic"><use href="#i-com"/></svg>4</span><span><svg class="ic"><use href="#i-heart"/></svg>134</span></div></div>
  </article>
  <article class="card" style="left:789px">
    <div class="ph" role="img" aria-label="Reporters holding microphones at a press event" style="background:linear-gradient(135deg,#8a2a2a,#5a4a4a 50%,#b9b0a8)"></div>
    <div class="in"><h3>News Title</h3><p>Lorem Ipsum is simply dummy text of the printing and typesetting industry.</p>
      <div class="meta"><span><svg class="ic"><use href="#i-cal"/></svg>April 21st, 2017</span><span><svg class="ic"><use href="#i-com"/></svg>4</span><span><svg class="ic"><use href="#i-heart"/></svg>134</span></div></div>
  </article>

  <div class="mini" style="left:77px;top:510px"><div class="ph" role="img" aria-label="Person flying a drone at sunset" style="background:linear-gradient(180deg,#a9b7c4,#b98a5a)"></div><div><h4>News Title</h4><div class="d"><svg class="ic"><use href="#i-cal"/></svg>April 22nd, 2017</div><p>Lorem Ipsum is simply dummy text of the...</p></div></div>
  <div class="mini" style="left:434px;top:510px"><div class="ph" role="img" aria-label="Flag waving against a blue sky" style="background:linear-gradient(135deg,#2b5aa8,#c9d6ea 55%,#b32020)"></div><div><h4>News Title</h4><div class="d"><svg class="ic"><use href="#i-cal"/></svg>April 22nd, 2017</div><p>Lorem Ipsum is simply dummy text of the...</p></div></div>
  <div class="mini" style="left:77px;top:640px"><div class="ph" role="img" aria-label="Glowing fiery swirl" style="background:radial-gradient(circle,#ffc24a,#b8460c 55%,#1a0a04)"></div><div><h4>News Title</h4><div class="d"><svg class="ic"><use href="#i-cal"/></svg>April 22nd, 2017</div><p>Lorem Ipsum is simply dummy text of the...</p></div></div>
  <div class="mini" style="left:434px;top:640px"><div class="ph" role="img" aria-label="Digital data network graphic" style="background:linear-gradient(135deg,#0d2740,#22607e 55%,#0b1a2a)"></div><div><h4>News Title</h4><div class="d"><svg class="ic"><use href="#i-cal"/></svg>April 22nd, 2017</div><p>Lorem Ipsum is simply dummy text of the...</p></div></div>
  <div class="mini" style="left:77px;top:770px"><div class="ph" role="img" aria-label="Group of business people standing together" style="background:linear-gradient(180deg,#e8e8e8,#5a5e6a)"></div><div><h4>News Title</h4><div class="d"><svg class="ic"><use href="#i-cal"/></svg>April 22nd, 2017</div><p>Lorem Ipsum is simply dummy text of the...</p></div></div>
  <div class="mini" style="left:434px;top:770px"><div class="ph" role="img" aria-label="Official signing documents at a desk" style="background:linear-gradient(180deg,#3a4a6a,#7a6a5a)"></div><div><h4>News Title</h4><div class="d"><svg class="ic"><use href="#i-cal"/></svg>April 22nd, 2017</div><p>Lorem Ipsum is simply dummy text of the...</p></div></div>

  <div class="abs subscribe">
    <h3>Subscribe</h3>
    <p>Get the recent popular stories<br>straight into your inbox</p>
    <div class="field" style="margin-top:26px">Name</div>
    <div class="field">E - Mail</div>
    <div class="btn">Submit</div>
  </div>
</section>

<section class="sec stories">
  <h2 class="abs h-sec" style="left:77px;top:56px">Top Stories</h2>
  <h2 class="abs h-sec" style="left:610px;top:56px">In Depth</h2>
  <div class="story" style="left:77px">
    <div class="ph" role="img" aria-label="Hands holding a tablet showing a cybersecurity plan" style="width:100%;height:100%;background:linear-gradient(135deg,#2a3a4a,#4d6a80 50%,#1a2530)"></div>
    <div class="cap"><h3>News Title</h3><p>Lorem Ipsum is simply dummy text of the printing and type setting industry.</p><div class="cat">Technology</div></div>
  </div>
  <div class="story" style="left:610px">
    <div class="ph" role="img" aria-label="Businesswoman in an office with colleagues behind her" style="width:100%;height:100%;background:linear-gradient(135deg,#8a9096,#c8ccd0 50%,#5a5f66)"></div>
    <div class="cap"><h3>News Title</h3><p>Lorem Ipsum is simply dummy text of the printing and type setting industry.</p><div class="cat">Business</div></div>
  </div>
</section>

<section class="sec video">
  <h2 class="abs h-sec" style="left:77px;top:55px">Featured Video</h2>
  <div class="abs player" role="img" aria-label="Video still of three officials applauding in front of a flag">
    <svg class="abs play" width="60" height="44" viewBox="0 0 60 44"><rect width="60" height="44" rx="10" fill="#d9100f"/><path d="M24 13v18l15-9z" fill="#fff"/></svg>
    <div class="abs cap"><span class="badge" style="text-transform:none">News</span><div class="d"><svg class="ic"><use href="#i-cal"/></svg>April 21st, 2017</div><h3>News Title</h3></div>
  </div>
  <div class="abs vbar">
    <div class="vtabs"><span class="on">Recommended</span><span>Most Watched</span><span>Latest</span></div>
    <div class="vitems">
      <div class="vitem"><div class="ph" role="img" aria-label="Historic building beside a river" style="background:linear-gradient(180deg,#5a8ac4,#c89a5a)"></div><div><h4>News Title</h4><div class="d">April 21st, 2017</div><span class="lbl">News</span></div></div>
      <div class="vitem"><div class="ph" role="img" aria-label="Flag waving" style="background:linear-gradient(135deg,#b32020,#eee 50%,#2b4a8a)"></div><div><h4>News Title</h4><div class="d">April 21st, 2017</div><span class="lbl">Business</span></div></div>
      <div class="vitem"><div class="ph" role="img" aria-label="Colourful nebula in space" style="background:linear-gradient(135deg,#1a1a5a,#c0402a 55%,#e0a040)"></div><div><h4>News Title</h4><div class="d">April 21st, 2017</div><span class="lbl">News</span></div></div>
    </div>
    <div class="abs vnext" style="color:#fff"><svg width="12" height="12"><use href="#i-r"/></svg></div>
  </div>
</section>

<section class="sec editor">
  <h2 class="abs h-sec" style="left:77px;top:55px">Editor's Picks</h2>
  <div class="abs" style="right:79px;top:56px;display:flex;gap:10px;color:var(--red)">
    <div class="redcirc"><svg width="12" height="12"><use href="#i-l"/></svg></div>
    <div class="redcirc" style="border-color:#999;color:#999"><svg width="12" height="12"><use href="#i-r"/></svg></div>
  </div>
  <div class="abs strip">
    <div class="ph" role="img" aria-label="Editor's pick story photo" style="background:#7a3a3a"><div class="ov"><h4>News Title</h4><div class="d">April 21st, 2017</div><p>Lorem Ipsum is simply dummy text of the printing and type.</p></div></div>
    <div class="ph" role="img" aria-label="Family gathered at a table" style="background:linear-gradient(135deg,#6a4a3a,#c8a080)"></div>
    <div class="ph" role="img" aria-label="Leader speaking at a podium" style="background:linear-gradient(180deg,#c8ccd0,#3a4a6a)"></div>
    <div class="ph" role="img" aria-label="Wall of video screens" style="background:linear-gradient(135deg,#2a2a30,#7a7a88 50%,#1a1a1e)"></div>
    <div class="ph" role="img" aria-label="Fiery glowing swirl" style="background:radial-gradient(circle,#ffd060,#c0500c 55%,#1a0a04)"></div>
  </div>
</section>

<section class="sec stay">
  <h2 class="h-sec">Stay Updated</h2>
  <p>Get the recent popular stories straight into your inbox</p>
  <div class="row"><div class="f">Name</div><div class="f">E - Mail</div><div class="b">SIGN UP</div></div>
</section>

<section class="sec weather">
  <span class="loc">London, United Kingdom</span>
  <span class="tmp"><svg width="32" height="22" viewBox="0 0 32 22"><circle cx="20" cy="8" r="6" fill="#fff"/><path d="M7 21a6 6 0 0 1 1-12 8 8 0 0 1 15 2 5 5 0 0 1 1 10z" fill="#fff"/></svg>10°</span>
  <div class="search"><div class="f">Search Meridian...</div><div class="g"><svg width="14" height="14" viewBox="0 0 18 18"><circle cx="7.5" cy="7.5" r="5.5" fill="none" stroke="#fff" stroke-width="2.2"/><path d="M12 12l5 5" stroke="#fff" stroke-width="2.2"/></svg></div></div>
</section>

<footer class="sec footer">
  <div class="col" style="left:77px"><h5>News</h5><ul><li>News Title</li><li>News Title</li><li>News Title</li><li>News Title</li><li>News Title</li><li>News Title</li></ul></div>
  <div class="col" style="left:350px"><h5>Business</h5><ul><li>Business Title</li><li>Business Title</li><li>Business Title</li><li>Business Title</li><li>Business Title</li><li>Business Title</li></ul></div>
  <div class="col" style="left:620px"><h5>Technology</h5><ul><li>Technology Title</li><li>Technology Title</li><li>Technology Title</li><li>Technology Title</li><li>Technology Title</li><li>Technology Title</li></ul></div>
  <div class="col" style="left:891px"><h5>More...</h5><ul><li>Title</li><li>Title</li><li>Title</li><li>Title</li><li>Title</li><li>Title</li></ul></div>
</footer>

<div class="sec bottom">
  <span class="copy">© Meridian - 2017. All Rights Reserved.</span>
  <div class="links"><span>Site Feedback</span><span>Corrections</span><span>Advertising Guidelines</span><span>Terms of Use</span><span>Privacy Policy</span></div>
</div>

</body>
</html>
```